Thornvale Group needs a business card design

We need a new business card design using the logo recently selected in a logo competition on Pixel Bazaar. Our business is a consultancy specializing in aviation and energy and the winning business card design will promote an image of precision and professionalism with creativity.

Please use the logo with the name on the front of the card and use a complementary font. Make the back white with either the light grey or dark grey logo.

Target Market(s)

Senior finance and legal leaders at aviation and energy companies

Industry/Entity Type

Management Consulting

Contact Information for Business Card

Peter Castrell
President
Thornvale Group

www.thornvalegroup.example

(555) 204-6391
pc@thornvalegroup.example

Requirements
Must have
• Professional font that goes well with the logo font

```html
<!DOCTYPE html>
<html lang="en">
<head>
<meta charset="utf-8">
<title>Thornvale Group – Business Card</title>
<link rel="stylesheet" href="https://fonts.googleapis.com/css2?family=Libre+Franklin:wght@400;600;700&display=swap">
<style>
  :root {
    --navy: #0d3f74;
    --slate: #5b5d60;
    --slate-dark: #3f4143;
    --paper: #ffffff;
    --paper-shade: #e4e5e6;
    --backdrop: #ecebe8;
    --ink-light: #ffffff;
  }
  * { margin: 0; padding: 0; box-sizing: border-box; }
  html, body {
    width: 1200px;
    height: 950px;
    overflow: hidden;
    background: var(--backdrop);
    font-family: "Libre Franklin", Arial, sans-serif;
  }
  .canvas {
    width: 1200px;
    height: 950px;
    display: flex;
    flex-direction: column;
    align-items: center;
    justify-content: center;
    gap: 50px;
  }
  .card {
    position: relative;
    width: 700px;
    height: 400px;
    overflow: hidden;
    box-shadow: 0 6px 18px rgba(0,0,0,0.18);
  }

  /* Back: white with name */
  .card-back {
    background: linear-gradient(120deg, var(--paper) 30%, var(--paper-shade) 100%);
    display: flex;
    align-items: center;
    justify-content: center;
  }
  .wordmark {
    display: flex;
    align-items: center;
    gap: 18px;
  }
  .wordmark-square {
    width: 26px;
    height: 26px;
    background: var(--navy);
  }
  .wordmark-name {
    color: var(--navy);
    font-weight: 400;
    font-size: 40px;
    letter-spacing: 4px;
    text-transform: uppercase;
  }

  /* Front: contact side */
  .card-front { background: var(--paper); }
  .card-front .shapes {
    position: absolute;
    inset: 0;
    width: 100%;
    height: 100%;
  }
  .contact {
    position: absolute;
    left: 42px;
    top: 30px;
    color: var(--ink-light);
  }
  .contact-name {
    font-weight: 700;
    font-size: 24px;
    line-height: 1.2;
    letter-spacing: 0.5px;
  }
  .contact-role {
    font-size: 15px;
    line-height: 1.2;
    margin-top: 2px;
  }
  .contact-company {
    margin-top: 16px;
    font-size: 15px;
    line-height: 1.3;
  }
  .contact-lines {
    list-style: none;
    margin-top: 6px;
    font-size: 15px;
    line-height: 1.45;
  }
  .contact-lines li {
    display: flex;
    align-items: center;
    gap: 8px;
  }
  .contact-lines svg {
    width: 14px;
    height: 14px;
    flex: none;
  }
</style>
</head>
<body>
<main class="canvas">

  <section class="card card-back" aria-label="Card back">
    <div class="wordmark">
      <span class="wordmark-square"></span>
      <span class="wordmark-name">Thornvale Group</span>
    </div>
  </section>

  <section class="card card-front" aria-label="Card front">
    <svg class="shapes" viewBox="0 0 700 400" preserveAspectRatio="none" aria-hidden="true">
      <defs>
        <linearGradient id="slate-fill" x1="0" y1="0" x2="1" y2="1">
          <stop offset="0" stop-color="#6a6c6f"/>
          <stop offset="1" stop-color="#3f4143"/>
        </linearGradient>
      </defs>
      <polygon points="0,0 620,0 97,400 0,400" fill="var(--navy)"/>
      <polygon points="642,0 700,0 700,400 357,400" fill="url(#slate-fill)"/>
    </svg>

    <div class="contact">
      <div class="contact-name">Peter Castrell</div>
      <div class="contact-role">President</div>
      <div class="contact-company">
        Thornvale Group LLC<br>
        Finance and Strategy Consulting<br>
        Aviation - Manufacturing - Energy
      </div>
      <ul class="contact-lines">
        <li>
          <svg viewBox="0 0 16 16" aria-hidden="true"><path fill="#fff" d="M3 1.5l3 .5 1 3-1.8 1.3a9 9 0 0 0 4.5 4.5L11 9l3 1 .5 3-1.5 1.5C7 14.5 1.5 9 1.5 3z"/></svg>
          (555) 204-6391
        </li>
        <li>
          <svg viewBox="0 0 16 16" aria-hidden="true"><rect x="1" y="3" width="14" height="10" fill="#fff"/><path d="M1.5 3.5L8 9l6.5-5.5" stroke="var(--navy)" stroke-width="1.4" fill="none"/></svg>
          pc@thornvalegroup.example
        </li>
        <li>
          <svg viewBox="0 0 16 16" aria-hidden="true"><circle cx="8" cy="8" r="7" fill="#fff"/><path d="M1 8h14M8 1c-3 3.5-3 10.5 0 14M8 1c3 3.5 3 10.5 0 14" stroke="var(--navy)" stroke-width="1.1" fill="none"/></svg>
          www.thornvalegroup.example
        </li>
      </ul>
    </div>
  </section>

</main>
</body>
</html>
```